Computer consultant business card

Bexil Software is a newly started computer consulting company. It's a small one-man company that provides mostly Vornix applications but also websites in collaboration with designers. I'm running this company on the side of full time university studies.

I want the final design to be clean and memorable. Be creative! :)

Some inspiration:
http://www.pixelmarta.com/design/48317
http://www.pixelmarta.com/design/2739164/business-card-design-by-frostlynk
http://www.pixelmarta.com/design/604281/business-card-design-by-koralind-vestrabanu

See attachment for my company logo.
Updates

I would like to thank everyone for submitting! I'll need a couple of days to review and ultimately select a design.

Target Market(s)

Non-technical entrepreneurs and small companies.

Industry/Entity Type

University

Requirements
Must have
• My company logo.
In any way, both colors from my logo.
First- and last name, e-mail and phone number.
Double-sided design.
Nice to have
• Something creative with the symbol in my logo

```html
<!DOCTYPE html>
<html lang="en">
<head>
<meta charset="utf-8">
<title>Bexil Software – Business Card</title>
<link rel="stylesheet" href="https://fonts.googleapis.com/css2?family=Mulish:ital,wght@0,400;0,700;0,800;1,700&display=swap">
<style>
  :root {
    --backdrop: #c7a982;
    --label: #1e1a16;
    --card-white: #ffffff;
    --ink-dark: #333333;
    --ink-mid: #4a4a4a;
    --brand-blue: #4a72bd;
    --brand-dark: #2e2e2e;
    --black: #050505;
    --slate-top: #2f3036;
    --slate-bottom: #4e5c82;
    --white: #ffffff;
  }
  * { box-sizing: border-box; margin: 0; padding: 0; }
  html, body { width: 1200px; height: 788px; overflow: hidden; }
  body {
    position: relative;
    background: var(--backdrop);
    font-family: "Mulish", "Century Gothic", sans-serif;
    color: var(--ink-dark);
  }
  .view-label {
    position: absolute;
    width: 525px;
    text-align: center;
    font-size: 20px;
    color: var(--label);
  }
  .card {
    position: absolute;
    width: 525px;
    height: 298px;
    border-radius: 22px;
    overflow: hidden;
    box-shadow: 2px 4px 10px rgba(0,0,0,.35);
  }
  .card--front, .card--back-light { background: var(--card-white); }
  .card--back-black {
    background:
      radial-gradient(ellipse 200px 120px at 160px 20px, rgba(110,110,110,.45), transparent 70%),
      radial-gradient(ellipse 170px 130px at 430px 260px, rgba(120,110,115,.45), transparent 70%),
      var(--black);
  }
  .card--back-slate {
    background: radial-gradient(ellipse 420px 260px at 50% 100%, var(--slate-bottom), var(--slate-top) 85%);
  }
  .swoosh { position: absolute; inset: 0; width: 100%; height: 100%; }
  .brand {
    position: absolute;
    display: flex;
    align-items: center;
  }
  .brand__mark {
    border-radius: 50%;
    background: var(--brand-blue);
    flex: none;
  }
  .brand__name {
    font-weight: 800;
    line-height: 1;
    letter-spacing: 1px;
  }
  .brand--small { left: 128px; top: 118px; gap: 22px; }
  .brand--small .brand__mark { width: 62px; height: 62px; }
  .brand--small .brand__name { font-size: 70px; color: var(--brand-dark); margin-top: -10px; }
  .brand--large { left: 104px; top: 92px; gap: 26px; }
  .brand--large .brand__mark { width: 96px; height: 96px; }
  .brand--large .brand__name { font-size: 98px; margin-top: -14px; }
  .card--back-light .brand__name { color: var(--brand-dark); }
  .card--back-black .brand__name, .card--back-slate .brand__name { color: var(--white); }
  .holder {
    position: absolute;
    top: 183px;
    width: 100%;
    text-align: center;
    font-size: 17px;
    font-weight: 700;
    color: var(--ink-dark);
  }
  .holder__role { font-size: 12.5px; font-weight: 400; }
  .contact {
    position: absolute;
    top: 236px;
    width: 100%;
    text-align: center;
    font-size: 15px;
    line-height: 20px;
    color: var(--ink-mid);
  }
  .contact__key { font-weight: 700; font-style: italic; }
  .web {
    position: absolute;
    top: 250px;
    width: 100%;
    text-align: center;
    font-size: 17px;
    letter-spacing: 3.5px;
  }
  .card--back-light .web { color: var(--ink-mid); }
  .card--back-black .web, .card--back-slate .web { color: var(--white); }
</style>
</head>
<body>
  <div class="view-label" style="left:55px; top:34px;">Front</div>
  <div class="view-label" style="left:622px; top:34px;">Back - 1</div>
  <div class="view-label" style="left:54px; top:405px;">Back - 2</div>
  <div class="view-label" style="left:622px; top:405px;">Back - 3</div>

  <section class="card card--front" style="left:55px; top:75px;">
    <svg class="swoosh" viewBox="0 0 525 298" aria-hidden="true">
      <path d="M440 0 Q500 8 525 55 L525 30 Q505 2 475 0 Z" fill="var(--brand-dark)"/>
      <path d="M420 0 Q495 15 525 80 L525 60 Q500 8 440 0 Z" fill="var(--brand-blue)"/>
      <path d="M0 250 Q40 285 120 298 L90 298 Q30 290 0 270 Z" fill="var(--brand-blue)"/>
      <path d="M0 270 Q30 290 90 298 L60 298 Q20 295 0 285 Z" fill="var(--brand-dark)"/>
    </svg>
    <div class="brand brand--small">
      <span class="brand__mark"></span>
      <span class="brand__name">bexil</span>
    </div>
    <p class="holder">First Name Last Name, <span class="holder__role">Designation</span></p>
    <p class="contact">
      <span class="contact__key">phone</span> : +12 345 6789<br>
      <span class="contact__key">email</span> : info@website.com
    </p>
  </section>

  <section class="card card--back-light" style="left:622px; top:75px;">
    <div class="brand brand--large">
      <span class="brand__mark"></span>
      <span class="brand__name">bexil</span>
    </div>
    <p class="web">www.website.com</p>
  </section>

  <section class="card card--back-black" style="left:54px; top:446px;" role="img" aria-label="Black card with soft metallic dot-pattern texture in the corners">
    <div class="brand brand--large">
      <span class="brand__mark"></span>
      <span class="brand__name">bexil</span>
    </div>
    <p class="web">www.website.com</p>
  </section>

  <section class="card card--back-slate" style="left:622px; top:446px;">
    <div class="brand brand--large">
      <span class="brand__mark"></span>
      <span class="brand__name">bexil</span>
    </div>
    <p class="web">www.website.com</p>
  </section>
</body>
</html>
```